Smack you in the face - Landing page for Residential Electrical Repairs (Searchly Ads)

I need an effective landing page for Searchly ads. The ads will target residential electrical repairs. Lighting Outages, Power Outages, Breakers Tripping, Outlets Not Working. I need a strong call to action to Call Us Now! Forms don't work well for us so we only need one form as a last option at the bottom of the page. We only work on homes. the website is https://www.vantor-wiring.example/
email is : support@vantor-wiring.example
Phone 555-217-4086

**This is about one focused service. Electrical Repairs - That includes Partial Power Outages, Outlets Not Working, Tripped Breakers, Electrical Panel repairs, and Fusebox Repairs. The area served will only be Greenville, SC. KOBA is the platform

Target Market(s)

Homeonwers in need of electrical repair

Industry/Entity Type

Residential Electricians

Coding

Coded - Design and coding required

Requirements
Must have
• Strong to action for phone calls, this landing page must grab action fast.
Nice to have
• Social proof with existing 5 start reviews for Searchly, Rately, TCB, and Friendnet
Should not have
• Should not be form based. I do not like the site's current them, please don't copy it. Make your own.

```html
<!DOCTYPE html>
<html lang="en">
<head>
<meta charset="utf-8">
<title>Vantor Wiring Service – Residential Electrical Repair</title>
<link rel="stylesheet" href="https://fonts.googleapis.com/css2?family=Archivo:wght@600;700;800;900&family=Montserrat:wght@400;500;600;700&display=swap">
<style>
:root{
  --blue:#1b8ec9;
  --blue-dark:#14638f;
  --blue-deep:#0d4a6e;
  --orange:#f26a21;
  --ink:#14171c;
  --text:#3b4048;
  --muted:#6a717b;
  --light:#eef2f6;
  --line:#9cc7e2;
  --footer:#0e1013;
  --white:#ffffff;
}
*{box-sizing:border-box;margin:0;padding:0}
html,body{width:1200px;height:4710px;overflow:hidden}
body{font-family:"Montserrat",sans-serif;color:var(--text);background:var(--white);position:relative}
.abs{position:absolute}
.eyebrow{font-size:15px;letter-spacing:2px;color:var(--blue);text-transform:uppercase;font-weight:500}
.title{font-family:"Archivo",sans-serif;font-weight:800;font-size:36px;color:var(--ink);text-transform:uppercase;line-height:1.15}
.title .hl{color:var(--blue)}
.bolt{display:inline-block;width:18px;height:34px;vertical-align:-4px;margin-left:2px}
.btn{display:inline-flex;align-items:center;justify-content:center;gap:8px;border-radius:30px;color:var(--white);font-weight:700;text-transform:uppercase;text-decoration:none;font-family:"Montserrat",sans-serif}
.btn-orange{background:var(--orange)}
.btn-blue{background:var(--blue-dark)}

/* header */
.site-header{top:0;left:0;width:1200px;height:88px;background:var(--white);z-index:5}
.brand{display:flex;align-items:center;gap:8px;font-family:"Archivo",sans-serif;font-weight:800;font-size:18px;color:var(--ink);text-transform:uppercase;letter-spacing:.3px;text-decoration:none;white-space:nowrap}
.brand-dot{width:16px;height:16px;border-radius:50%;background:var(--blue);flex:none}
.site-header .brand{position:absolute;left:100px;top:33px}
.main-nav{position:absolute;left:326px;top:36px;display:flex;gap:62px;font-size:13px;font-weight:600;color:var(--ink)}
.main-nav a{color:inherit;text-decoration:none;position:relative}
.main-nav a.active::after{content:"";position:absolute;left:0;right:0;bottom:-10px;height:2px;background:var(--orange)}
.header-call{position:absolute;right:0;top:0;width:270px;height:88px;background:var(--blue);clip-path:polygon(28px 0,100% 0,100% 100%,0 100%);color:var(--white);display:flex;align-items:center;gap:12px;padding-left:55px}
.header-call small{display:block;font-size:11px;font-weight:500}
.header-call strong{font-size:19px;font-weight:700}
.phone-ico{width:32px;height:32px;border-radius:50%;background:var(--white);display:flex;align-items:center;justify-content:center;flex:none}

/* hero */
.hero{top:88px;left:0;width:1200px;height:702px;overflow:hidden}
.hero-photo{position:absolute;inset:0;background:linear-gradient(100deg,#0f5b85 0%,#1b86b8 40%,#3d7f9c 62%,#9aa7ae 85%,#c8c6c0 100%)}
.hero-copy{position:absolute;left:100px;top:170px;color:var(--white)}
.hero-copy .eyebrow{color:#e9f4fb;font-size:18px}
.hero-title{font-family:"Archivo",sans-serif;font-weight:800;font-size:46px;line-height:60px;text-transform:uppercase;margin-top:12px}
.hero-title .box{background:var(--blue);padding:0 12px;margin-left:14px}
.hero .btn{margin-top:30px;width:214px;height:52px;font-size:15px}
.hero-edge{position:absolute;left:0;bottom:0;width:1200px;height:90px}

/* services */
.services{top:790px;left:0;width:1200px;height:710px;background:var(--light)}
.services .eyebrow,.reviews .eyebrow{text-align:center;position:absolute;left:0;width:1200px}
.services .title,.reviews .title{text-align:center;position:absolute;left:0;width:1200px}
.svc-card{position:absolute;width:306px;height:188px;background:var(--white);border:1.5px solid var(--line);border-radius:4px;text-align:center;padding:66px 24px 0}
.svc-card h3{font-size:15px;font-weight:700;color:var(--ink);margin-bottom:10px}
.svc-card p{font-size:11.5px;line-height:17px;color:var(--muted)}
.svc-card.active{background:var(--blue);border-color:var(--blue)}
.svc-card.active h3,.svc-card.active p{color:var(--white)}
.svc-card.active .btn{margin-top:12px;height:28px;width:132px;font-size:9px}
.svc-icon{position:absolute;left:50%;top:-32px;margin-left:-38px;width:76px;height:76px;border-radius:50%;background:var(--blue);border:5px solid var(--white);display:flex;align-items:center;justify-content:center}
.svc-card.active .svc-icon{background:var(--orange)}

/* about */
.about{top:1500px;left:0;width:1200px;height:631px;background:var(--white)}
.about-media{position:absolute;left:113px;top:58px;width:436px;height:545px}
.about-copy{position:absolute;left:638px;top:84px;width:490px}
.about-copy .title{font-size:37px;margin-top:10px}
.about-copy p{font-size:14.5px;line-height:23px;margin-top:22px}

/* cta band */
.cta-band{top:2131px;left:0;width:1200px;height:104px;background:var(--orange)}
.cta-band .msg{position:absolute;left:156px;top:36px;font-family:"Archivo",sans-serif;font-weight:800;font-size:26px;color:var(--white);text-transform:uppercase}
.cta-band .blue{position:absolute;right:0;top:0;width:440px;height:104px;background:var(--blue);clip-path:polygon(60px 0,100% 0,100% 100%,0 100%)}
.cta-band .num{position:absolute;left:850px;top:30px;display:flex;align-items:center;gap:14px;color:var(--white);font-weight:700;font-size:25px}

/* why */
.why{top:2235px;left:0;width:1200px;height:600px;background:linear-gradient(180deg,#f4f7fa,#e8eef4);overflow:hidden}
.why-photo{position:absolute;left:560px;top:0;width:640px;height:545px;background:radial-gradient(ellipse at 55% 45%,#c9a06a 0%,#8c8c86 35%,#d8dde2 70%,rgba(232,238,244,0) 100%)}
.why-copy{position:absolute;left:124px;top:98px}
.why-copy .title{font-size:31px;margin-top:8px}
.why-list{list-style:none;margin-top:28px}
.why-list li{display:flex;align-items:center;gap:14px;height:60px;margin-bottom:24px}
.why-ico{width:60px;height:60px;border-radius:50%;background:var(--white);box-shadow:0 2px 8px rgba(0,0,0,.08);display:flex;align-items:center;justify-content:center;flex:none}
.why-list h4{font-size:15px;font-weight:700;color:var(--ink)}
.why-list p{font-size:12px;color:var(--muted);margin-top:4px}
.why-edge{position:absolute;left:0;bottom:0;width:1200px;height:90px}

/* reviews */
.reviews{top:2835px;left:0;width:1200px;height:494px;background:var(--white)}
.review{position:absolute;top:159px;width:316px;height:240px;border:1.5px solid var(--line);border-radius:6px;padding:38px 36px 0 38px}
.review q{display:block;font-size:12.5px;font-style:italic;line-height:19px;color:var(--ink);quotes:"“" "”"}
.review .who{margin-top:14px;font-size:12.5px;font-weight:700;color:var(--ink)}
.stars{color:var(--orange);font-size:15px;letter-spacing:1px}
.platform{position:absolute;right:26px;bottom:22px;display:flex;align-items:center;gap:6px;font-size:12px;font-weight:700;color:var(--ink)}
.platform i{width:14px;height:14px;border-radius:50%;background:var(--blue);display:block}
.arrow{position:absolute;top:265px;width:20px;height:34px}

/* area */
.area{top:3329px;left:0;width:1200px;height:503px;background:var(--light)}
.area-copy{position:absolute;left:134px;top:100px;width:420px}
.area-copy .title{font-size:37px;margin-top:8px}
.area-copy p{font-size:14px;line-height:27px;margin-top:22px}
.area .btn{margin-top:28px;width:234px;height:54px;font-size:17px;text-transform:uppercase}
.area-map{position:absolute;left:609px;top:64px;width:507px;height:402px;background:linear-gradient(135deg,#e3ecf4,#d5e2ee);border-radius:8px}

/* contact */
.contact{top:3832px;left:0;width:1200px;height:631px;background:var(--blue);overflow:hidden}
.contact-photo{position:absolute;inset:0;background:linear-gradient(120deg,#1b8ec9 0%,#2a7eaa 45%,#1f6f9b 70%,#1b8ec9 100%);opacity:.9}
.contact-copy{position:absolute;left:141px;top:120px;color:var(--white);width:440px}
.contact-copy .eyebrow{color:#e1f1fb;font-size:17px}
.contact-copy .title{color:var(--white);font-size:36px;margin-top:8px}
.contact-copy p{font-size:15px;line-height:27px;margin-top:14px}
.contact-item{display:flex;align-items:center;gap:18px;margin-top:30px}
.contact-item .circ{width:56px;height:56px;border-radius:50%;background:var(--white);display:flex;align-items:center;justify-content:center;flex:none}
.contact-item small{display:block;font-size:16px;text-transform:uppercase}
.contact-item strong{font-size:22px;font-weight:700}
.contact-item span.mail{font-size:18px}
.contact-form{position:absolute;left:603px;top:69px;width:489px;height:412px;background:var(--white);border-radius:4px;padding:42px 44px 0 46px}
.field{display:flex;align-items:center;gap:8px;width:399px;height:45px;border:1.5px solid #8bb9d7;margin-bottom:9px;padding-left:16px;font-size:12px;color:var(--ink)}
.field.area-field{height:80px;align-items:flex-start;padding-top:12px}
.contact-form .btn{width:142px;height:36px;font-size:12px;margin-top:8px}
.contact-edge{position:absolute;left:0;bottom:0;width:1200px;height:110px}

/* footer */
.site-footer{top:4463px;left:0;width:1200px;height:247px;background:var(--footer);color:var(--white)}
.site-footer .brand{position:absolute;left:146px;top:82px;color:var(--white)}
.foot-nav{position:absolute;left:348px;top:86px;display:flex;gap:56px;font-size:15px;font-weight:600}
.site-footer .btn{position:absolute;left:922px;top:72px;width:186px;height:42px;font-size:14px}
.foot-rule{position:absolute;left:0;top:165px;width:1200px;height:1px;background:#2a2e34}
.copyright{position:absolute;left:158px;top:197px;font-size:12px;color:#cfd3d8}
.copyright a{color:inherit}
.socials{position:absolute;left:973px;top:190px;display:flex;gap:10px}
.socials span{width:32px;height:32px;border-radius:50%;border:1.5px solid var(--white);display:block}
</style>
</head>
<body>

<svg width="0" height="0" style="position:absolute">
  <defs>
    <symbol id="bolt" viewBox="0 0 18 34"><polygon points="12,0 2,19 9,19 5,34 17,12 10,12 15,0" fill="#1b8ec9"/></symbol>
    <symbol id="bolt-w" viewBox="0 0 18 34"><polygon points="12,0 2,19 9,19 5,34 17,12 10,12 15,0" fill="#ffffff"/></symbol>
    <symbol id="phone" viewBox="0 0 24 24"><path d="M6.6 10.8a15 15 0 0 0 6.6 6.6l2.2-2.2c.3-.3.7-.4 1-.2 1.1.4 2.3.6 3.6.6.6 0 1 .4 1 1V20c0 .6-.4 1-1 1A17 17 0 0 1 3 4c0-.6.4-1 1-1h3.5c.6 0 1 .4 1 1 0 1.3.2 2.5.6 3.6.1.3 0 .7-.2 1z"/></symbol>
  </defs>
</svg>

<header class="site-header abs">
  <a class="brand" href="#"><span class="brand-dot"></span>Vantor Wiring</a>
  <nav class="main-nav">
    <a class="active" href="#">HOME</a><a href="#">ABOUT US</a><a href="#">SERVICES</a><a href="#">REVIEWS</a><a href="#">CONTACT</a>
  </nav>
  <div class="header-call">
    <span class="phone-ico"><svg width="18" height="18" fill="#1b8ec9"><use href="#phone"/></svg></span>
    <div><small>24/7 CALL US NOW</small><strong>555-217-4086</strong></div>
  </div>
</header>

<section class="hero abs">
  <div class="hero-photo" role="img" aria-label="Electrician working on a residential breaker panel"></div>
  <div class="hero-copy">
    <p class="eyebrow">Vantor Wiring Services</p>
    <h1 class="hero-title">Trusted source<br>for<span class="box">Electrical</span><br>solution</h1>
    <a class="btn btn-orange" href="tel:5552174086">Call us now <svg class="bolt" style="width:12px;height:24px"><use href="#bolt-w"/></svg></a>
  </div>
  <svg class="hero-edge" viewBox="0 0 1200 90" preserveAspectRatio="none">
    <polygon points="0,90 0,84 600,42 615,26 1200,0 1200,90" fill="#f26a21"/>
    <polygon points="0,90 620,50 640,30 1200,14 1200,90" fill="#eef2f6"/>
  </svg>
</section>

<section class="services abs">
  <p class="eyebrow" style="top:54px">What we do</p>
  <h2 class="title" style="top:82px">Electrical <span class="hl">Repair</span><svg class="bolt"><use href="#bolt"/></svg></h2>

  <article class="svc-card" style="left:126px;top:192px">
    <span class="svc-icon"><svg width="34" height="34"><use href="#bolt-w"/></svg></span>
    <h3>Partial Power Outages</h3>
    <p>Lorem ipsum dolor sit amet, consectetur adipiscing elit, sed do eiusmod tempor incididunt ut labore et dolore</p>
  </article>
  <article class="svc-card active" style="left:446px;top:192px">
    <span class="svc-icon"><svg width="34" height="22" viewBox="0 0 34 22"><rect x="1" y="1" width="32" height="20" rx="4" fill="none" stroke="#fff" stroke-width="2"/><rect x="7" y="6" width="8" height="10" rx="2" fill="none" stroke="#fff" stroke-width="2"/><rect x="19" y="6" width="8" height="10" rx="2" fill="none" stroke="#fff" stroke-width="2"/></svg></span>
    <h3>Outlets Not Working</h3>
    <p>Lorem ipsum dolor sit amet, consectetur adipiscing elit, sed do eiusmod</p>
    <a class="btn btn-orange" href="tel:5552174086">Call us now</a>
  </article>
  <article class="svc-card" style="left:768px;top:192px">
    <span class="svc-icon"><svg width="30" height="34" viewBox="0 0 30 34"><rect x="2" y="2" width="26" height="30" rx="3" fill="none" stroke="#fff" stroke-width="2"/><line x1="8" y1="10" x2="22" y2="10" stroke="#fff" stroke-width="2"/><line x1="8" y1="17" x2="22" y2="17" stroke="#fff" stroke-width="2"/><line x1="8" y1="24" x2="22" y2="24" stroke="#fff" stroke-width="2"/></svg></span>
    <h3>Tripped Breakers</h3>
    <p>Lorem ipsum dolor sit amet, consectetur adipiscing elit, sed do eiusmod tempor incididunt ut labore et dolore</p>
  </article>
  <article class="svc-card" style="left:287px;top:441px">
    <span class="svc-icon"><svg width="30" height="34" viewBox="0 0 30 34"><rect x="2" y="2" width="26" height="30" rx="2" fill="none" stroke="#fff" stroke-width="2"/><rect x="7" y="7" width="6" height="6" fill="#fff"/><rect x="17" y="7" width="6" height="6" fill="#fff"/><rect x="7" y="17" width="6" height="6" fill="#fff"/><rect x="17" y="17" width="6" height="6" fill="#fff"/></svg></span>
    <h3>Electrical Panel repairs</h3>
    <p>Lorem ipsum dolor sit amet, consectetur adipiscing elit, sed do eiusmod tempor incididunt ut labore et dolore</p>
  </article>
  <article class="svc-card" style="left:607px;top:441px">
    <span class="svc-icon"><svg width="30" height="34" viewBox="0 0 30 34"><rect x="2" y="2" width="26" height="30" rx="3" fill="none" stroke="#fff" stroke-width="2"/><polygon points="17,7 10,19 15,19 12,28 20,15 15,15 18,7" fill="#fff"/></svg></span>
    <h3>Fusebox Repairs</h3>
    <p>Lorem ipsum dolor sit amet, consectetur adipiscing elit, sed do eiusmod tempor incididunt ut labore et dolore</p>
  </article>
</section>

<section class="about abs">
  <svg class="about-media" viewBox="0 0 436 545" role="img" aria-label="Smiling electrician with a cap, inset of a technician at a panel">
    <defs><linearGradient id="aboutGrad" x1="0" y1="0" x2="1" y2="1"><stop offset="0" stop-color="#b7c7cf"/><stop offset=".5" stop-color="#4f7f9c"/><stop offset="1" stop-color="#1f2a33"/></linearGradient></defs>
    <polygon points="218,8 428,128 428,400 218,520 8,400 8,128" fill="none" stroke="#1b8ec9" stroke-width="3"/>
    <polygon points="218,24 412,136 412,392 218,504 24,392 24,136" fill="url(#aboutGrad)"/>
    <polygon points="330,320 430,378 430,490 330,545 232,490 232,378" fill="#ffffff"/>
    <polygon points="330,332 420,384 420,484 330,534 242,484 242,384" fill="#9fb4c4"/>
  </svg>
  <div class="about-copy">
    <p class="eyebrow">Who we are</p>
    <h2 class="title">About Vantor<br><span class="hl">Electrical Repair</span><svg class="bolt"><use href="#bolt"/></svg></h2>
    <p>At Vantor Wiring, EV Chargers, &amp; Generators, your electrical emergency is our urgency. We have Licensed Electricians in Greenville, SC, Raleigh, NC, and Charlotte, NC, ensuring top-tier service for every call. We've built our reputation as the go-to Emergency Electrician for homeowners in need.</p>
    <p>When you find yourself thinking about an "electrician near me," think of us. While many electrical contractors chase after large-scale construction and commercial building projects, we prioritize you – the homeowner. We're committed to delivering unbeatable same-day service for all your residential electrical repairs, EV chargers, and Generator installations.</p>
  </div>
</section>

<section class="cta-band abs">
  <p class="msg">Need electrical repair service now!</p>
  <div class="blue"></div>
  <div class="num"><span class="phone-ico" style="width:36px;height:36px"><svg width="20" height="20" fill="#1b8ec9"><use href="#phone"/></svg></span>555-217-4086</div>
</section>

<section class="why abs">
  <div class="why-photo" role="img" aria-label="Hand testing a wall outlet with a digital multimeter"></div>
  <div class="why-copy">
    <p class="eyebrow">Why we are</p>
    <h2 class="title">Why choose Vantor<br><span class="hl">Electrical Service</span><svg class="bolt"><use href="#bolt"/></svg></h2>
    <ul class="why-list">
      <li><span class="why-ico"><svg width="28" height="28" viewBox="0 0 28 28"><rect x="3" y="5" width="22" height="20" rx="2" fill="none" stroke="#1b8ec9" stroke-width="2"/><line x1="3" y1="11" x2="25" y2="11" stroke="#1b8ec9" stroke-width="2"/></svg></span><div><h4>On-Time Appointments</h4><p>Lorem ipsum dolor sit amet, consectetur</p></div></li>
      <li><span class="why-ico"><svg width="30" height="30" viewBox="0 0 30 30"><circle cx="15" cy="15" r="12" fill="none" stroke="#1b8ec9" stroke-width="2"/><text x="15" y="19" font-size="9" font-family="Montserrat,sans-serif" font-weight="700" fill="#1b8ec9" text-anchor="middle">24/7</text></svg></span><div><h4>Same-Day Service</h4><p>Lorem ipsum dolor sit amet, consectetur adipi</p></div></li>
      <li><span class="why-ico"><svg width="30" height="30" viewBox="0 0 30 30"><circle cx="15" cy="15" r="12" fill="none" stroke="#1b8ec9" stroke-width="2"/><polyline points="9,15 13,19 21,11" fill="none" stroke="#1b8ec9" stroke-width="2.5"/></svg></span><div><h4>100% Satisfaction Guarantee</h4><p>Lorem ipsum dolor sit amet, consect</p></div></li>
    </ul>
  </div>
  <svg class="why-edge" viewBox="0 0 1200 90" preserveAspectRatio="none">
    <polygon points="0,90 1200,90 1200,40" fill="#ffffff"/>
    <polygon points="0,86 590,46 605,30 1200,10 1200,28 640,46 620,62 0,90" fill="#1b8ec9"/>
  </svg>
</section>

<section class="reviews abs">
  <p class="eyebrow" style="top:56px">Testimonials</p>
  <h2 class="title" style="top:84px">Customer <span class="hl">Reviews</span><svg class="bolt"><use href="#bolt"/></svg></h2>
  <svg class="arrow" style="left:55px" viewBox="0 0 20 34"><polyline points="16,3 4,17 16,31" fill="none" stroke="#8a9097" stroke-width="3"/></svg>
  <svg class="arrow" style="left:1132px" viewBox="0 0 20 34"><polyline points="4,3 16,17 4,31" fill="none" stroke="#8a9097" stroke-width="3"/></svg>
  <article class="review" style="left:117px">
    <q>Lorem ipsum dolor sit amet, consectetur adipiscing elit, sed do eiusmod tempor incididunt ut labore et dolore magna aliqua Quis ipsum suspendisse ultrices gravida Risus commodo viverra maecenas</q>
    <p class="who">Dana Mercer</p><p class="stars">★★★★★</p>
    <span class="platform"><i></i>Searchly</span>
  </article>
  <article class="review" style="left:450px">
    <q>Lorem ipsum dolor sit amet, consectetur adipiscing elit, sed do eiusmod tempor incididunt ut labore et dolore magna aliqua Quis ipsum suspendisse ultrices gravida Risus commodo viverra maecenas</q>
    <p class="who">Dana Mercer</p><p class="stars">★★★★★</p>
    <span class="platform"><i style="background:#d0302a"></i>Rately</span>
  </article>
  <article class="review" style="left:781px">
    <q>Lorem ipsum dolor sit amet, consectetur adipiscing elit, sed do eiusmod tempor incididunt ut labore et dolore magna aliqua Quis ipsum suspendisse ultrices gravida Risus commodo viverra maecenas</q>
    <p class="who">Dana Mercer</p><p class="stars">★★★★★</p>
    <span class="platform"><i></i>Friendnet</span>
  </article>
</section>

<section class="area abs">
  <div class="area-copy">
    <p class="eyebrow">Where we serve</p>
    <h2 class="title">Area we <span class="hl">Serve</span><svg class="bolt"><use href="#bolt"/></svg></h2>
    <p>Lorem ipsum dolor sit amet, consectetur adipiscing elit, sed do eiusmod tempor incididunt ut labore et dolore magna aliqua. Quis ipsum suspendisse ultrices gravida. Risus commodo viverra maecenas</p>
    <a class="btn btn-blue" href="tel:5552174086"><svg width="18" height="18" fill="#fff"><use href="#phone"/></svg>Call us now</a>
  </div>
  <div class="area-map" role="img" aria-label="County map of South Carolina showing the service area"></div>
</section>

<section class="contact abs">
  <div class="contact-photo" role="img" aria-label="Electrician standing beside a service van, tinted blue"></div>
  <div class="contact-copy">
    <p class="eyebrow">Get in touch</p>
    <h2 class="title">Contact us<svg class="bolt"><use href="#bolt-w"/></svg></h2>
    <p>Lorem ipsum dolor sit amet consectetur adipiscing elit, sed do eiusmod tempor incididunt</p>
    <div class="contact-item"><span class="circ"><svg width="26" height="26" fill="#1b8ec9"><use href="#phone"/></svg></span><div><small>Phone number</small><strong>555-217-4086</strong></div></div>
    <div class="contact-item"><span class="circ"><svg width="26" height="20" viewBox="0 0 26 20"><rect x="1" y="1" width="24" height="18" rx="2" fill="#1b8ec9"/><polyline points="2,3 13,11 24,3" fill="none" stroke="#fff" stroke-width="2"/></svg></span><div><small>Email us</small><span class="mail">support@vantor-wiring.example</span></div></div>
  </div>
  <form class="contact-form">
    <label class="field">👤 First name</label>
    <label class="field">👤 Last name</label>
    <label class="field"><svg width="12" height="12" fill="#1b8ec9"><use href="#phone"/></svg>Phone number</label>
    <label class="field">✉ Email address</label>
    <label class="field area-field">Comments</label>
    <button type="button" class="btn btn-orange" style="border:0">Submit ›</button>
  </form>
  <svg class="contact-edge" viewBox="0 0 1200 110" preserveAspectRatio="none">
    <polygon points="0,110 0,95 640,45 660,25 1200,0 1200,110" fill="#f26a21"/>
    <polygon points="0,110 0,104 660,60 680,42 1200,26 1200,110" fill="#0e1013"/>
  </svg>
</section>

<footer class="site-footer abs">
  <a class="brand" href="#"><span class="brand-dot"></span>Vantor Wiring</a>
  <nav class="foot-nav"><span>HOME</span><span>ABOUT US</span><span>SERVICES</span><span>CONTACT US</span></nav>
  <a class="btn btn-orange" href="tel:5552174086"><svg width="16" height="16" fill="#fff"><use href="#phone"/></svg>555-217-4086</a>
  <div class="foot-rule"></div>
  <p class="copyright">© 2023 <a href="https://www.vantor-wiring.example/">Vantor Wiring Service</a>. All Right Reserved</p>
  <div class="socials"><span aria-label="Friendnet"></span><span aria-label="Social profile"></span><span aria-label="Photo profile"></span></div>
</footer>

</body>
</html>
```